Site Redesign in WORDPRESS for a Aerial Survey Company

We are looking for an updated look to our website that reflects our aerial drone services. Our company is changing directions from helping to provide legal documentation for companies to operate UAVs for commercial operations, to now providing Aerial Data Collection services. We need the new website to focus on this new direction.

Wordpress Design (Uncoded - PSD layout only)

Current site: http://tornwickaviation.com/
Business card attached

VISUAL
********
The new pages should be visually top-notch, appealing, and more user-friendly to navigate, and represent our professionalism and level of expertise. We love the use of images, both great photography and technical. Our specialty is the use of Aerial LiDAR.

Our current site uses the Mallow template.

Colors: I've attached the Pantone for our logo colors

Fonts: Simple, clean and professional. We are not worried about specific fonts so long as they tie or compliment our logo.

STRUCTURE
****************
In the attached document I have laid out the pages we would like to have and the content outline of the content these pages will include.

We're happy to answer you questions in the comments and to provide quick feedback and additional info if necessary.

Target Market(s)

Agricultural and Engineering firms

Industry/Entity Type

Agribusiness

Coding

Coded - Design and coding required

Number of Pages Required

5+ page

Font styles to use
Sans Serif

Colors
0392cd
9bcb3c
ffffff

Requirements
Must have
• We need at a minimum a design with the Home/Landing, Services, and about. Need to be able to adapt the site as we add new services and increase our partnerships.
• Please provide in WordPress format.
• Links to social media: Facebook, Twitter, Instagram
Nice to have
• We like parrallax, but in the end it's about the overall feel of the site.
Should not have
• Please, professional designs only.

```html
<!DOCTYPE html>
<html lang="en">
<head>
<meta charset="utf-8">
<title>Tornwick Aviation</title>
<link href="https://fonts.googleapis.com/css2?family=Arimo:wght@400;700&family=Open+Sans:wght@400;600;700&display=swap" rel="stylesheet">
<style>
:root{
  --green:#5aa83f;
  --green-dark:#4a9532;
  --blue:#3b87c9;
  --blue-deep:#2e76b8;
  --beige:#ecebe3;
  --ink:#222;
  --muted:#555;
  --white:#fff;
  --dark:#2a3036;
  --orange:#f26522;
}
*{box-sizing:border-box;margin:0;padding:0}
html,body{width:1200px;height:3020px;overflow:hidden}
body{font-family:"Open Sans",Arial,sans-serif;color:var(--ink);background:var(--white);position:relative}
.section{position:absolute;left:0;width:1200px;overflow:hidden}
.abs{position:absolute}
.center{text-align:center}
.heading{font-family:"Arimo",Arial,sans-serif;font-weight:700;font-size:24px;letter-spacing:.5px;text-transform:uppercase;position:absolute;left:0;width:1200px;text-align:center}
.section-mark{position:absolute;left:584px;width:32px;height:32px;border-radius:3px;background:var(--white);border:3px solid var(--green)}

/* header */
.site-header{top:0;height:90px;background:var(--white);border-top:5px solid var(--green)}
.brand{position:absolute;left:98px;top:24px;display:flex;align-items:center;gap:12px}
.brand-square{width:34px;height:34px;background:var(--green);border-radius:3px}
.brand-name{font-family:"Arimo",Arial,sans-serif;font-weight:700;font-size:22px;color:var(--blue-deep);text-transform:uppercase;letter-spacing:.5px}
.main-nav{position:absolute;right:120px;top:34px;display:flex;gap:26px;font-size:14px;font-weight:600}
.main-nav a{color:var(--ink);text-decoration:none}
.main-nav a.active{color:var(--green)}
.search{position:absolute;right:98px;top:36px}

/* hero */
.hero{top:90px;height:430px;background:linear-gradient(180deg,#7d8f92 0%,#5f7473 40%,#4d5f5e 70%,#3c4747 100%)}
.hero-photo{position:absolute;inset:0;background:linear-gradient(120deg,#5d7a57 0%,#708889 35%,#8a999a 55%,#5b6a6b 80%,#3f4a4c 100%)}
.hero-kicker{top:168px;font-family:"Arimo",Arial,sans-serif;font-weight:700;font-size:28px;color:var(--white);letter-spacing:.5px}
.hero-title{top:208px;font-family:"Arimo",Arial,sans-serif;font-weight:700;font-size:54px;color:var(--white)}
.hero-caption{left:0;width:1200px}
.dots{left:558px;top:380px;display:flex;gap:6px}
.dots span{width:16px;height:16px;border-radius:50%;border:2px solid var(--white)}
.dots span.on{background:var(--green);border-color:#a9d48f}

/* services */
.services{top:520px;height:520px;background:linear-gradient(180deg,var(--blue) 0%,#4a90c9 50%,#3a7fbc 100%);color:var(--white)}
.services .heading{top:78px;color:var(--white)}
.service{position:absolute;width:260px;margin-left:-130px;text-align:center}
.service-icon{width:106px;height:106px;margin:0 auto;border-radius:50%;background:var(--white);border:5px solid var(--green);display:flex;align-items:center;justify-content:center}
.service-label{margin-top:10px;font-size:14.5px;font-weight:700}

/* capabilities */
.capabilities{top:1040px;height:520px;background:var(--beige)}
.capabilities .heading{top:90px;color:var(--ink)}
.cap{position:absolute;width:440px;text-align:center}
.cap-photo{width:400px;height:176px;margin:0 auto;border-radius:6px;background:radial-gradient(ellipse at center,#4a4a4f 0%,#8b8a88 45%,var(--beige) 72%)}
.cap h3{margin-top:32px;font-family:"Arimo",Arial,sans-serif;font-size:17px;font-weight:700;text-transform:uppercase}
.cap p{margin:14px auto 0;width:340px;font-size:12.5px;line-height:22px;color:var(--muted)}
.read-more{display:block;margin-top:12px;font-size:12px;font-weight:700;color:var(--green);text-decoration:none}
.cap-divider{left:599px;top:160px;width:1px;height:300px;background:#d6d4ca}

/* about */
.about{top:1560px;height:505px;background:var(--green);color:var(--white)}
.about .heading{top:88px;color:var(--white)}
.member{position:absolute;top:126px;width:260px;margin-left:-130px;text-align:center}
.portrait{width:178px;height:178px;margin:0 auto;border-radius:50%;border:5px solid var(--white);background:linear-gradient(180deg,#bdbdbd,#6f6f6f)}
.member h4{margin-top:14px;font-size:15.5px;font-weight:700}
.member .role{font-size:12.5px;margin-top:3px}
.member .bio{font-size:12px;line-height:22px;margin:8px auto 0;width:220px}
.member .read-more{color:var(--white);margin-top:10px;font-size:11.5px}

/* partners */
.partners{top:2065px;height:360px;background:var(--white)}
.partners .heading{top:86px;color:var(--ink)}
.partner{position:absolute;top:150px;width:470px;text-align:center}
.partner-name{height:46px;display:flex;align-items:center;justify-content:center;font-family:"Arimo",Arial,sans-serif;font-weight:700;font-size:20px}
.partner-name.alt{font-size:32px;color:var(--orange);letter-spacing:1px}
.partner p{margin-top:10px;font-size:12.5px;line-height:22px;color:var(--muted)}
.partner a{display:inline-block;margin-top:12px;font-size:14px;color:var(--blue-deep)}

/* contact */
.contact{top:2425px;height:525px;background:linear-gradient(180deg,#3a4148 0%,#2b3137 45%,#3c4a52 75%,#1f2428 100%);color:var(--white)}
.contact-scene{position:absolute;inset:0;background:radial-gradient(ellipse at 78% 30%,rgba(120,130,140,.35),transparent 55%)}
.contact .heading{top:80px;color:var(--white)}
.col-title{font-size:14px;font-weight:700;text-transform:uppercase}
.form{left:98px;top:118px;width:632px}
.field-label{font-size:11px;font-weight:600;margin-top:22px}
.input{margin-top:10px;width:632px;height:34px;background:var(--white)}
.input.area{height:84px}
.submit{position:absolute;right:0;top:362px;width:94px;height:40px;border:2px solid var(--white);font-size:12px;font-weight:700;display:flex;align-items:center;justify-content:center}
.info{left:808px;top:118px;width:300px}
.info-row{display:flex;gap:24px;margin-top:26px;font-size:12px;line-height:20px}
.info-row:first-of-type{margin-top:20px}
.info-icon{flex:none;width:38px;height:38px;border-radius:50%;border:2px solid var(--white);display:flex;align-items:center;justify-content:center}
.social-title{margin-top:36px}
.social{display:flex;gap:12px;margin-top:20px}
.social span{width:26px;height:26px;border-radius:4px;background:var(--white)}

.footer{top:2950px;height:70px;background:var(--white);font-size:12px;color:var(--muted);text-align:center;padding-top:30px}
</style>
</head>
<body>

<header class="section site-header">
  <div class="brand"><span class="brand-square"></span><span class="brand-name">Tornwick Aviation</span></div>
  <nav class="main-nav">
    <a class="active" href="#">Home</a><a href="#">Services</a><a href="#">Capabilities</a><a href="#">About Us</a><a href="#">Partners</a><a href="#">Blog &amp; Upcoming Events</a><a href="#">Contact Us</a>
  </nav>
  <svg class="search" width="16" height="16" viewBox="0 0 16 16"><circle cx="6.5" cy="6.5" r="5" fill="none" stroke="#222" stroke-width="2"/><line x1="10.5" y1="10.5" x2="15" y2="15" stroke="#222" stroke-width="2.4"/></svg>
</header>

<section class="section hero">
  <div class="hero-photo" role="img" aria-label="Aerial view of a coastal bridge crossing a bay beside a wooded island"></div>
  <div class="abs hero-caption hero-kicker center">WE DEVELOP COMPLETE SOLUTIONS</div>
  <div class="abs hero-caption hero-title center">NOT JUST TEMPLATES</div>
  <div class="abs dots"><span class="on"></span><span></span><span></span><span></span></div>
</section>

<section class="section services">
  <div class="section-mark" style="top:36px"></div>
  <h2 class="heading">Our Services</h2>

  <div class="service" style="left:290px;top:56px">
    <div class="service-icon"><svg width="50" height="50" viewBox="0 0 50 50"><path d="M34 8c-10 2-17 10-19 20l7 7c10-2 18-9 20-19z" fill="#5aa83f"/><circle cx="31" cy="19" r="4" fill="#fff"/><path d="M15 28l-6 2 4-8 6-1zM22 35l-2 6 8-4 1-6z" fill="#5aa83f"/></svg></div>
    <div class="service-label">Exploration, Oil, Gas, &amp; Mineral</div>
  </div>
  <div class="service" style="left:910px;top:56px">
    <div class="service-icon"><svg width="50" height="50" viewBox="0 0 50 50" fill="none" stroke="#5aa83f" stroke-width="3"><path d="M25 7l9 15M41 35H23M9 35l8-14"/><text x="25" y="32" font-size="14" fill="#5aa83f" stroke="none" text-anchor="middle" font-family="Arimo,Arial,sans-serif" font-weight="700">$</text></svg></div>
    <div class="service-label">Section 333 Exemptions</div>
  </div>

  <div class="service" style="left:151px;top:202px">
    <div class="service-icon"><svg width="52" height="50" viewBox="0 0 52 50" fill="none" stroke="#5aa83f" stroke-width="3"><path d="M6 40c8-14 16-20 40-22M10 42c8-10 18-14 36-14M4 44h44"/><rect x="12" y="10" width="12" height="10" fill="#5aa83f"/></svg></div>
    <div class="service-label">Precision Agriculture</div>
  </div>
  <div class="service" style="left:429px;top:202px">
    <div class="service-icon"><svg width="54" height="40" viewBox="0 0 54 40"><rect x="4" y="10" width="34" height="20" fill="#5aa83f"/><path d="M38 16h8l5 8v6H38z" fill="#5aa83f"/><rect x="8" y="4" width="24" height="4" fill="#5aa83f"/><circle cx="14" cy="32" r="4" fill="#fff" stroke="#5aa83f" stroke-width="2"/><circle cx="42" cy="32" r="4" fill="#fff" stroke="#5aa83f" stroke-width="2"/></svg></div>
    <div class="service-label">Public Services</div>
  </div>
  <div class="service" style="left:598px;top:202px">
    <div class="service-icon"><svg width="52" height="52" viewBox="0 0 52 52" fill="none" stroke="#5aa83f" stroke-width="3"><circle cx="12" cy="12" r="7"/><circle cx="40" cy="12" r="7"/><circle cx="12" cy="40" r="7"/><circle cx="40" cy="40" r="7"/><path d="M17 17l18 18M35 17L17 35"/><rect x="21" y="21" width="10" height="10" fill="#5aa83f"/></svg></div>
    <div class="service-label">FLLIR/IR</div>
  </div>
  <div class="service" style="left:771px;top:202px">
    <div class="service-icon"><svg width="52" height="46" viewBox="0 0 52 46"><circle cx="14" cy="11" r="8" fill="#5aa83f"/><circle cx="32" cy="11" r="8" fill="#5aa83f"/><rect x="6" y="20" width="30" height="20" fill="#5aa83f"/><path d="M36 26l12-6v20l-12-6z" fill="#5aa83f"/></svg></div>
    <div class="service-label">Video &amp; Still Images</div>
  </div>
  <div class="service" style="left:1049px;top:202px">
    <div class="service-icon"><svg width="50" height="50" viewBox="0 0 50 50" fill="none" stroke="#5aa83f" stroke-width="3"><path d="M6 12h10l8 4 8-4h12v32H32l-8-4-8 4H6z"/><path d="M25 10c-5 0-8 3-8 7 0 5 8 13 8 13s8-8 8-13c0-4-3-7-8-7z" fill="#5aa83f" stroke="none"/></svg></div>
    <div class="service-label">GIS &amp; Mapping</div>
  </div>

  <div class="service" style="left:290px;top:344px">
    <div class="service-icon"><svg width="52" height="50" viewBox="0 0 52 50"><path d="M4 44V22l12 8v-8l12 8v-8l12 8V6h8v38z" fill="#5aa83f"/><rect x="10" y="36" width="6" height="4" fill="#fff"/><rect x="22" y="36" width="6" height="4" fill="#fff"/></svg></div>
    <div class="service-label">Commercial &amp; Industrial Inspections</div>
  </div>
  <div class="service" style="left:910px;top:344px">
    <div class="service-icon"><svg width="56" height="40" viewBox="0 0 56 40"><rect x="4" y="6" width="18" height="4" rx="2" fill="#5aa83f"/><rect x="34" y="6" width="18" height="4" rx="2" fill="#5aa83f"/><path d="M12 10v6h32v-6" stroke="#5aa83f" stroke-width="3" fill="none"/><rect x="18" y="14" width="20" height="10" rx="3" fill="#5aa83f"/><circle cx="28" cy="30" r="4" fill="#5aa83f"/></svg></div>
    <div class="service-label">UAV Flight Training &amp; Consulting</div>
  </div>
</section>

<section class="section capabilities">
  <div class="section-mark" style="top:44px"></div>
  <h2 class="heading">Capabilities</h2>
  <div class="abs cap-divider"></div>
  <article class="cap" style="left:80px;top:114px">
    <div class="cap-photo" role="img" aria-label="Multi-rotor survey drone with eight arms"></div>
    <h3>Drones</h3>
    <p>A comprehensive package for those just starting out. Includes all documents needed to operate efficiently and professionally.</p>
    <a class="read-more" href="#">READ MORE &gt;&gt;</a>
  </article>
  <article class="cap" style="left:672px;top:114px">
    <div class="cap-photo" role="img" aria-label="Heavy-lift drone carrying a gimbal camera"></div>
    <h3>Cameras</h3>
    <p>A comprehensive package for those just starting out. Includes all documents needed to operate efficiently and professionally.</p>
    <a class="read-more" href="#">READ MORE &gt;&gt;</a>
  </article>
</section>

<section class="section about">
  <div class="section-mark" style="top:40px"></div>
  <h2 class="heading">About Us</h2>
  <div class="member" style="left:193px">
    <div class="portrait" role="img" aria-label="Portrait of the chief executive"></div>
    <h4>Lorna Vickery</h4><div class="role">( CEO )</div>
    <p class="bio">Specializes in Supply Chain and Network Optimization</p>
    <a class="read-more" href="#">READ MORE &gt;&gt;</a>
  </div>
  <div class="member" style="left:461px">
    <div class="portrait" role="img" aria-label="Portrait of the president"></div>
    <h4>Dale Harmon</h4><div class="role">( President )</div>
    <p class="bio">Operations &amp; Regulatory Specialist and an Airline Transport Pilot</p>
    <a class="read-more" href="#">READ MORE &gt;&gt;</a>
  </div>
  <div class="member" style="left:735px">
    <div class="portrait" role="img" aria-label="Portrait of the director of GIS"></div>
    <h4>Rufus</h4><div class="role">( Director of GIS )</div>
    <p class="bio">Helicopter Pilot and Aerial Media Specialist</p>
    <a class="read-more" href="#">READ MORE &gt;&gt;</a>
  </div>
  <div class="member" style="left:1003px">
    <div class="portrait" role="img" aria-label="Portrait of a partner"></div>
    <h4>Peter Caldwell</h4><div class="role">( Partner )</div>
    <p class="bio">FAA Deputy Director of Flight Standards, Retired, Helicopter Pilot</p>
    <a class="read-more" href="#">READ MORE &gt;&gt;</a>
  </div>
</section>

<section class="section partners">
  <div class="section-mark" style="top:40px"></div>
  <h2 class="heading">Partners</h2>
  <div class="partner" style="left:116px">
    <div class="partner-name">Caldwell Aerospace Consulting, LLC</div>
    <p>Peter Caldwell Consulting, LLC offers unique and unparalleled expertise that encompasses and connects multiple aerospace disciplines. Experience includes engineering, certification, flight test..</p>
    <a href="#">http://www.pcaldaerospace.aero/</a>
  </div>
  <div class="partner" style="left:606px">
    <div class="partner-name alt">HALDREN</div>
    <p>We have several major partnerships already in place, with U.S. and foreign companies, which collectively give us excellent capabilities and expert skill levels in all areas of aviation, unmanned systems..</p>
    <a href="#">http://haldren.co/</a>
  </div>
</section>

<section class="section contact">
  <div class="contact-scene" role="img" aria-label="Drone silhouetted against a dusk sky over hills"></div>
  <div class="section-mark" style="top:30px"></div>
  <h2 class="heading">Contact Us</h2>
  <form class="abs form">
    <div class="col-title">Contact Form</div>
    <div class="field-label">NAME :</div><div class="input"></div>
    <div class="field-label">EMAIL :</div><div class="input"></div>
    <div class="field-label">MESSAGE :</div><div class="input area"></div>
    <div class="submit">SUBMIT</div>
  </form>
  <div class="abs info">
    <div class="col-title">Contact Information</div>
    <div class="info-row">
      <span class="info-icon"><svg width="14" height="18" viewBox="0 0 14 18"><path d="M7 0C3 0 0 3 0 7c0 5 7 11 7 11s7-6 7-11c0-4-3-7-7-7z" fill="#fff"/><circle cx="7" cy="7" r="2.5" fill="#2b3137"/></svg></span>
      <span>Tornwick Aviation<br>2210 Marlow Ave<br>Fallbrook, CA 92028</span>
    </div>
    <div class="info-row">
      <span class="info-icon"><svg width="18" height="13" viewBox="0 0 18 13"><rect width="18" height="13" rx="1" fill="#fff"/><path d="M1 1l8 6 8-6" stroke="#2b3137" stroke-width="1.6" fill="none"/></svg></span>
      <span style="padding-top:9px">lvickery@tornwickaviation.com</span>
    </div>
    <div class="info-row">
      <span class="info-icon"><svg width="16" height="16" viewBox="0 0 16 16"><path d="M3 1l3 3-2 2c1 2 3 4 5 5l2-2 3 3-2 3C6 15 1 10 0 3z" fill="#fff"/></svg></span>
      <span style="padding-top:9px">+1 855-555-0142</span>
    </div>
    <div class="col-title social-title">Social</div>
    <div class="social"><span></span><span></span><span></span></div>
  </div>
</section>

<footer class="section footer">Copyrights © 2016, Tornwick Aviation . All Rights Reserved.</footer>

</body>
</html>
```